Business Card Design

We need a business card designed for our new company. Prefer a black card with white logo & writing.

Contact Information for Business Card

Ted Galloway, address: 7-4812 Fernhollow Road, Abbotsford, BC, V3K 8R2, Office Phone: 604-712-3390, Cell: 604-947-2164, Email: ted@resinworkshub.ca

Colors

Designer to choose only greyscale colors for use in the design.

```html
<!DOCTYPE html>
<html lang="en">
<head>
<meta charset="utf-8">
<title>Resinworks Hub – Business Card</title>
<link href="https://fonts.googleapis.com/css2?family=Poppins:wght@300;400;700&display=swap" rel="stylesheet">
<style>
  :root {
    --backdrop: #1d1d1e;
    --card: #222225;
    --card-edge: #34343a;
    --ink: #ffffff;
    --ink-soft: #d9d9dc;
    --rule: #8a8a8f;
    --emboss: #46464c;
  }
  * { box-sizing: border-box; margin: 0; padding: 0; }
  html, body {
    width: 1200px; height: 711px; overflow: hidden;
    background: var(--backdrop);
    font-family: "Poppins", sans-serif;
    color: var(--ink);
  }
  .stage {
    width: 1200px; height: 711px;
    display: flex; align-items: center; justify-content: center; gap: 40px;
  }
  .card {
    width: 520px; height: 297px;
    background: var(--card);
    border: 1px solid var(--card-edge);
    border-radius: 4px;
    position: relative;
  }
  .card--front { display: flex; align-items: center; justify-content: center; }
  .brand { display: flex; align-items: center; gap: 12px; }
  .brand__mark { width: 22px; height: 22px; background: currentColor; }
  .brand__name {
    font-weight: 700; font-size: 30px; letter-spacing: 1px;
    text-transform: uppercase; line-height: 1;
  }
  .card--front .brand { color: var(--emboss); }
  .card--back { display: flex; align-items: center; }
  .card--back .brand { width: 248px; justify-content: center; color: var(--ink); }
  .card--back .brand__name { font-size: 21px; }
  .card--back .brand__mark { width: 16px; height: 16px; }
  .divider { width: 1px; height: 150px; background: var(--rule); }
  .contact { padding-left: 28px; }
  .contact__name { font-size: 25px; font-weight: 300; line-height: 1.1; }
  .contact__name strong { font-weight: 700; }
  .contact__role { font-size: 11px; font-weight: 400; color: var(--ink-soft); margin-bottom: 12px; }
  .contact__address { font-size: 11px; font-weight: 300; line-height: 1.45; margin-bottom: 12px; }
  .contact__list { list-style: none; font-size: 11px; font-weight: 300; line-height: 1.75; }
  .contact__list li { display: flex; align-items: center; gap: 9px; }
  .contact__list svg { width: 12px; height: 12px; flex: none; }
</style>
</head>
<body>
<main class="stage">
  <section class="card card--front">
    <div class="brand">
      <span class="brand__mark"></span>
      <span class="brand__name">Resinworks Hub</span>
    </div>
  </section>

  <section class="card card--back">
    <div class="brand">
      <span class="brand__mark"></span>
      <span class="brand__name">Resinworks Hub</span>
    </div>
    <div class="divider"></div>
    <div class="contact">
      <p class="contact__name"><strong>Ted</strong> Galloway</p>
      <p class="contact__role">Founder &amp; CEO</p>
      <p class="contact__address">7-4812 Fernhollow Road,<br>Abbotsford, BC, V3K 8R2.</p>
      <ul class="contact__list">
        <li>
          <svg viewBox="0 0 24 24" fill="#fff"><path d="M6.6 10.8a15 15 0 0 0 6.6 6.6l2.2-2.2c.3-.3.7-.4 1-.2 1.1.4 2.3.6 3.6.6.6 0 1 .4 1 1V20c0 .6-.4 1-1 1A17 17 0 0 1 3 4c0-.6.4-1 1-1h3.5c.6 0 1 .4 1 1 0 1.3.2 2.5.6 3.6.1.3 0 .7-.2 1z"/></svg>
          604-712-3390
        </li>
        <li>
          <svg viewBox="0 0 24 24" fill="none" stroke="#fff" stroke-width="2"><rect x="6" y="2" width="12" height="20" rx="2"/><circle cx="12" cy="18" r="1" fill="#fff"/></svg>
          604-947-2164
        </li>
        <li>
          <svg viewBox="0 0 24 24" fill="none" stroke="#fff" stroke-width="2"><circle cx="12" cy="12" r="9"/><path d="M3 12h18M12 3c3 3 3 15 0 18M12 3c-3 3-3 15 0 18"/></svg>
          www.resinworkshub.ca
        </li>
        <li>
          <svg viewBox="0 0 24 24" fill="none" stroke="#fff" stroke-width="2"><rect x="3" y="5" width="18" height="14" rx="1"/><path d="M3 6l9 7 9-7"/></svg>
          ted@resinworkshub.ca
        </li>
      </ul>
    </div>
  </section>
</main>
</body>
</html>
```